New PowerPoint Design Project

I need a company powerpoint template for my company, Varnok (see design file logo attached), that has a number of templated slides with an exciting supporting colour palette. Needs to have header and footer sections, tables in colour which support the logo colour, bar and line charts, dot point slides and image (placeholders) slides. Logo is attached.
The primary use of this template is to pitch for new work - ie about us page, previous clients page, then a breakdown of services offered in a table format with prices etc...
Updates

Hi everyone
Please see some example PPT templates that provide more of a guide as to what I need.

Thanks
Leopold

Font styles to use
Serif
Sans Serif

Colors
0054AA
0677BA
7BADD7
CADEEF
E8F1F8
00AB8E
00BBA5
67D7C9
C6EFE9
E9F9F6
59FF00
82FF00
B8FF75
E3FFCB
F4FFEA
FFC000
F8CF3A
FAE287
FDF2CF
FEFAEE

```html
<!DOCTYPE html>
<html lang="en">
<head>
<meta charset="utf-8">
<title>Varnok Presentation Template</title>
<link rel="stylesheet" href="https://fonts.googleapis.com/css2?family=Marcellus&family=Cormorant+Garamond:ital,wght@1,400&family=Inter:wght@300;400;600&display=swap">
<style>
:root{
  --forest:#0f3b31;
  --forest-deep:#0a2b24;
  --forest-mid:#2f5a4f;
  --leaf:#6aa84f;
  --leaf-soft:#8fd18a;
  --moss:#3f7a4f;
  --cyan:#00a9c4;
  --gold:#d9a431;
  --stage:#1d5a55;
  --ink:#1e3d36;
  --grey:#8a8f8d;
  --line:#e4e8e6;
  --white:#ffffff;
}
*{box-sizing:border-box;margin:0;padding:0}
html,body{width:1200px;height:2623px;overflow:hidden;background:var(--white);font-family:"Inter",sans-serif;color:var(--ink)}
.stage{position:absolute;left:0;top:0;width:1200px;height:945px;background:linear-gradient(160deg,#1c5450,#22675f)}
.hero{position:absolute;transform:scale(1.2755);transform-origin:0 0;box-shadow:0 10px 30px rgba(0,0,0,.35)}
.slide{position:absolute;width:392px;height:220px;overflow:hidden;background:var(--white);box-shadow:0 2px 6px rgba(0,0,0,.12)}
.abs{position:absolute}
.bar{position:absolute;left:0;top:0;width:100%;height:27px;background:var(--forest)}
.brand{position:absolute;left:8px;top:9px;font-family:"Marcellus",serif;font-size:8px;color:var(--gold);letter-spacing:.5px}
.copy{position:absolute;left:0;right:0;top:11px;text-align:center;font-size:3.5px;color:#cfd8d4}
.dot{position:absolute;right:8px;top:9px;width:9px;height:9px;border-radius:50%;background:var(--gold)}
.foot{position:absolute;left:0;right:0;bottom:6px;text-align:center;font-size:3px;color:var(--grey)}
.title{font-family:"Marcellus",serif;font-size:12px;line-height:1.3;color:var(--ink)}
.title em{font-family:"Cormorant Garamond",serif;font-style:italic;font-size:13px}
.tiny{font-size:3.4px;line-height:1.5;color:var(--grey)}
.tiny-w{font-size:3.4px;line-height:1.5;color:#d6e2dd}
.ph-car{background:radial-gradient(ellipse at 55% 62%,#35b24f 0%,#145a2a 30%,#07140c 70%,#030604 100%)}
.ph-streak{background:linear-gradient(115deg,#061a14 0%,#0d3a28 30%,#1f7a3c 45%,#0a2a1e 55%,#0f4d2e 70%,#04110c 100%)}
.ph-face{background:linear-gradient(180deg,#d9c2a6,#8a6a4e 60%,#2d2a28)}
.ph-hair{background:linear-gradient(180deg,#e8d2b0,#c49a6a 55%,#8a6040)}
.circ{position:absolute;width:12px;height:12px;border-radius:50%;background:var(--forest);color:#fff;font-size:5px;text-align:center;line-height:12px}
.card{position:absolute;background:#fff;border-radius:4px;box-shadow:0 2px 6px rgba(0,0,0,.12)}
.btn{position:absolute;height:7px;border-radius:2px;background:var(--forest);color:#fff;font-size:3.2px;line-height:7px;padding-left:4px}
.cap{font-size:4px;color:var(--ink)}
.gold-word{font-family:"Marcellus",serif;color:var(--gold)}
</style>
</head>
<body>

<!-- Feature slides laid flat -->
<section class="stage">
  <div class="slide hero" style="left:60px;top:30px;background:var(--forest-deep)">
    <div class="abs ph-streak" role="img" aria-label="Dark green light streak background" style="inset:0"></div>
    <div class="abs gold-word" style="left:0;right:0;top:70px;text-align:center;font-size:40px">VARNOK</div>
    <div class="abs" style="left:0;right:0;top:122px;text-align:center;font-family:Marcellus,serif;font-size:10px;color:#e6ece9">VARNOK Presentation Template</div>
  </div>
  <div class="slide hero" style="left:640px;top:30px">
    <div class="abs ph-streak" role="img" aria-label="Dark green light streak background" style="left:0;top:0;width:392px;height:138px"></div>
    <div class="abs gold-word" style="right:6px;top:104px;font-size:34px">VARNOK</div>
    <div class="abs title" style="left:14px;top:155px;font-size:26px">Divider title Goes Here</div>
    <div class="foot">Insert your footer title here</div>
  </div>
  <div class="slide hero" style="left:60px;top:331px;background:var(--forest)">
    <div class="brand" style="top:7px">VARNOK</div><div class="copy" style="top:9px">Copyright © VARNOK. All rights reserved.</div><div class="dot" style="top:6px"></div>
    <div class="abs ph-car" role="img" aria-label="Green sports car photo" style="left:6px;top:35px;width:380px;height:178px;border-radius:8px"></div>
    <div class="abs" style="left:28px;top:142px;font-family:Marcellus,serif;font-size:16px;color:#fff">Analyzing Case Studies for</div>
    <div class="abs" style="left:20px;top:162px;background:var(--leaf);padding:0 8px;font-family:Marcellus,serif;font-size:16px;color:#fff">Business Growth</div>
    <div class="abs tiny-w" style="left:268px;top:144px;width:90px">Sed ut perspiciatis unde omnis iste natus error sit voluptatem accusantium doloremque laudantium, totam rem.</div>
    <div class="abs" style="left:268px;top:172px;width:38px;height:8px;border-radius:4px;background:var(--leaf);color:#fff;font-size:3.5px;text-align:center;line-height:8px">Let's Talk</div>
    <div class="abs" style="left:309px;top:172px;width:8px;height:8px;border-radius:50%;background:var(--leaf)"></div>
  </div>
  <div class="slide hero" style="left:640px;top:331px">
    <div class="bar"><div class="brand">VARNOK</div><div class="copy">Copyright © VARNOK. All rights reserved.</div><div class="dot"></div></div>
    <div class="abs" style="left:0;top:27px;width:392px;height:68px;background:var(--forest)"></div>
    <div class="abs title" style="left:20px;top:40px;color:#fff">Case Studies of<br><em>Entrepreneurial Success</em></div>
    <div class="abs tiny-w" style="left:230px;top:45px;width:140px">Sed ut perspiciatis unde omnis iste natus error sit voluptatem accusantium doloremque laudantium, totam rem aperiam, eaque ipsa quae ab illo.</div>
    <div class="card" style="left:20px;top:88px;width:108px;height:40px"></div><div class="circ" style="left:27px;top:102px">A</div><div class="abs cap" style="left:44px;top:94px">Service One</div><div class="abs tiny" style="left:44px;top:101px;width:76px">Sed ut perspiciatis unde omnis iste natus error sit voluptatem.</div>
    <div class="card" style="left:135px;top:88px;width:108px;height:40px"></div><div class="circ" style="left:142px;top:102px">B</div><div class="abs cap" style="left:159px;top:94px">Service Two</div><div class="abs tiny" style="left:159px;top:101px;width:76px">Sed ut perspiciatis unde omnis iste natus error sit voluptatem.</div>
    <div class="card" style="left:250px;top:88px;width:108px;height:40px"></div><div class="circ" style="left:257px;top:102px">C</div><div class="abs cap" style="left:274px;top:94px">Service Three</div><div class="abs tiny" style="left:274px;top:101px;width:76px">Sed ut perspiciatis unde omnis iste natus error sit voluptatem.</div>
    <div class="card" style="left:20px;top:145px;width:108px;height:40px"></div><div class="circ" style="left:27px;top:159px">D</div><div class="abs cap" style="left:44px;top:151px">Service Four</div><div class="abs tiny" style="left:44px;top:158px;width:76px">Sed ut perspiciatis unde omnis iste natus error sit voluptatem.</div>
    <div class="card" style="left:135px;top:145px;width:108px;height:40px"></div><div class="circ" style="left:142px;top:159px">E</div><div class="abs cap" style="left:159px;top:151px">Service Five</div><div class="abs tiny" style="left:159px;top:158px;width:76px">Sed ut perspiciatis unde omnis iste natus error sit voluptatem.</div>
    <div class="card" style="left:250px;top:145px;width:108px;height:40px"></div><div class="circ" style="left:257px;top:159px">F</div><div class="abs cap" style="left:274px;top:151px">Service Six</div><div class="abs tiny" style="left:274px;top:158px;width:76px">Sed ut perspiciatis unde omnis iste natus error sit voluptatem.</div>
    <div class="foot">Insert your footer title here</div>
  </div>
  <div class="slide hero" style="left:350px;top:632px;background:var(--forest)">
    <div class="abs gold-word" style="left:18px;top:24px;font-size:38px">VARNOK</div>
    <div class="abs" style="left:18px;top:62px;font-family:Marcellus,serif;font-size:32px;color:#fff">Thank You</div>
    <div class="abs" style="left:210px;top:118px;width:70px;height:1px;background:#7fa39a"></div>
    <div class="abs tiny-w" style="left:292px;top:110px;width:88px">Sed ut perspiciatis unde omnis iste natus error sit voluptatem accusantium laudantium, totam rem.</div>
    <div class="abs" style="left:0;top:146px;width:392px;height:74px;background:var(--forest-mid)"></div>
    <div class="abs tiny-w" style="left:70px;top:172px;text-align:center;font-size:4.5px">Address<br>482 Linden Row<br>Harlow, MA 02194</div>
    <div class="abs tiny-w" style="left:175px;top:172px;text-align:center;font-size:4.5px">Email<br>hello@varnok.com<br>team@varnok.com</div>
    <div class="abs tiny-w" style="left:285px;top:172px;text-align:center;font-size:4.5px">Phone &amp; Fax<br>+1 (555) 014 2290<br>555 014 2291</div>
  </div>
</section>

<!-- Row 1 -->
<div class="slide" style="left:4px;top:983px;background:var(--forest-deep)">
  <div class="abs ph-streak" role="img" aria-label="Dark green light streak background" style="inset:0"></div>
  <div class="abs gold-word" style="left:0;right:0;top:70px;text-align:center;font-size:40px">VARNOK</div>
  <div class="abs" style="left:0;right:0;top:122px;text-align:center;font-family:Marcellus,serif;font-size:10px;color:#e6ece9">VARNOK Presentation Template</div>
</div>
<div class="slide" style="left:403px;top:983px">
  <div class="abs ph-streak" role="img" aria-label="Dark green light streak background" style="left:0;top:0;width:392px;height:138px"></div>
  <div class="abs gold-word" style="right:6px;top:104px;font-size:34px">VARNOK</div>
  <div class="abs title" style="left:14px;top:155px;font-size:26px">Divider title Goes Here</div>
  <div class="foot">Insert your footer title here</div>
</div>
<div class="slide" style="left:802px;top:983px;background:var(--forest)">
  <div class="brand" style="top:7px">VARNOK</div><div class="copy" style="top:9px">Copyright © VARNOK. All rights reserved.</div><div class="dot" style="top:6px"></div>
  <div class="abs ph-car" role="img" aria-label="Green sports car photo" style="left:6px;top:35px;width:380px;height:178px;border-radius:8px"></div>
  <div class="abs" style="left:28px;top:142px;font-family:Marcellus,serif;font-size:16px;color:#fff">Analyzing Case Studies for</div>
  <div class="abs" style="left:20px;top:162px;background:var(--leaf);padding:0 8px;font-family:Marcellus,serif;font-size:16px;color:#fff">Business Growth</div>
  <div class="abs tiny-w" style="left:268px;top:144px;width:90px">Sed ut perspiciatis unde omnis iste natus error sit voluptatem accusantium doloremque laudantium, totam rem.</div>
  <div class="abs" style="left:268px;top:172px;width:38px;height:8px;border-radius:4px;background:var(--leaf);color:#fff;font-size:3.5px;text-align:center;line-height:8px">Let's Talk</div>
  <div class="abs" style="left:309px;top:172px;width:8px;height:8px;border-radius:50%;background:var(--leaf)"></div>
</div>

<!-- Row 2 -->
<div class="slide" style="left:4px;top:1212px">
  <div class="bar"><div class="brand">VARNOK</div><div class="copy">Copyright © VARNOK. All rights reserved.</div><div class="dot"></div></div>
  <div class="abs title" style="left:20px;top:34px">Agenda Office</div>
  <div class="abs ph-car" role="img" aria-label="Green sports car in studio light" style="left:195px;top:27px;width:197px;height:193px"></div>
  <div class="abs" style="left:20px;top:96px;width:260px;height:92px;background:rgba(47,90,79,.92)"></div>
  <div class="abs" style="left:42px;top:112px;font-family:Marcellus,serif;font-size:11px;color:#fff">01.</div>
  <div class="abs" style="left:70px;top:113px;font-size:5px;color:#fff">Welcome Introductions<br><span style="font-size:3.5px">9:00 - 9:20</span></div>
  <div class="abs" style="left:42px;top:149px;font-family:Marcellus,serif;font-size:11px;color:#fff">02.</div>
  <div class="abs" style="left:70px;top:151px;font-size:5px;color:#fff">Review Yesterday's Tasks<br><span style="font-size:3.5px">9:20 - 9:00</span></div>
  <div class="abs" style="left:172px;top:112px;font-family:Marcellus,serif;font-size:11px;color:#fff">03.</div>
  <div class="abs" style="left:198px;top:113px;font-size:5px;color:#fff">Discussion of Today's<br><span style="font-size:3.5px">9:00 - 9:30</span></div>
  <div class="abs" style="left:172px;top:149px;font-family:Marcellus,serif;font-size:11px;color:#fff">04.</div>
  <div class="abs" style="left:198px;top:151px;font-size:5px;color:#fff">Team Member Updates<br><span style="font-size:3.5px">9:30 - 20:30</span></div>
  <div class="foot">Insert your footer title here</div>
</div>
<div class="slide" style="left:403px;top:1212px">
  <div class="bar"><div class="brand">VARNOK</div><div class="copy">Copyright © VARNOK. All rights reserved.</div><div class="dot"></div></div>
  <div class="abs title" style="left:20px;top:33px">Case Studies in Decision<br><em>Making Excellence</em></div>
  <div class="abs" style="left:330px;top:43px;width:10px;height:10px;border-radius:50%;background:var(--forest);color:#fff;font-size:6px;text-align:center;line-height:10px">←</div>
  <div class="abs" style="left:343px;top:43px;width:10px;height:10px;border-radius:50%;background:var(--forest);color:#fff;font-size:6px;text-align:center;line-height:10px">→</div>
  <div class="abs ph-car" role="img" aria-label="Green car photo" style="left:18px;top:78px;width:110px;height:112px;border-radius:5px"></div>
  <div class="abs" style="left:133px;top:78px;width:112px;height:50px;border-radius:5px;background:var(--leaf)"></div>
  <div class="abs" style="left:250px;top:78px;width:112px;height:50px;border-radius:5px;background:var(--cyan)"></div>
  <div class="abs" style="left:133px;top:131px;width:112px;height:59px;border-radius:5px;background:var(--cyan)"></div>
  <div class="abs" style="left:250px;top:131px;width:112px;height:59px;border-radius:5px;background:var(--leaf)"></div>
  <div class="abs" style="left:140px;top:84px;width:9px;height:9px;border-radius:2px;background:rgba(255,255,255,.8)"></div>
  <div class="abs" style="left:257px;top:84px;width:9px;height:9px;border-radius:2px;background:rgba(255,255,255,.8)"></div>
  <div class="abs" style="left:140px;top:137px;width:9px;height:9px;border-radius:2px;background:rgba(255,255,255,.8)"></div>
  <div class="abs" style="left:257px;top:137px;width:9px;height:9px;border-radius:2px;background:rgba(255,255,255,.8)"></div>
  <div class="abs" style="left:234px;top:82px;color:#fff;font-size:6px">↗</div><div class="abs" style="left:351px;top:82px;color:#fff;font-size:6px">↗</div>
  <div class="abs" style="left:234px;top:135px;color:#fff;font-size:6px">↗</div><div class="abs" style="left:351px;top:135px;color:#fff;font-size:6px">↗</div>
  <div class="abs" style="left:140px;top:112px;font-size:4px;color:#fff;width:70px">Case Studies of Technology-Driven Change</div>
  <div class="abs" style="left:257px;top:102px;font-size:4px;color:#fff;width:70px">Case Studies in Market Success</div>
  <div class="abs" style="left:140px;top:175px;font-size:4px;color:#fff;width:70px">Case Studies in Market Success</div>
  <div class="abs" style="left:257px;top:175px;font-size:4px;color:#fff;width:80px">Case Studies of Technology-Driven Change</div>
</div>
<div class="slide" style="left:802px;top:1212px">
  <div class="bar"><div class="brand">VARNOK</div><div class="copy">Copyright © VARNOK. All rights reserved.</div><div class="dot"></div></div>
  <div class="abs title" style="left:24px;top:40px">Case Studies of<br><em>Entrepreneurial Success</em></div>
  <div class="abs tiny" style="left:230px;top:48px;width:140px">Sed ut perspiciatis unde omnis iste natus error sit voluptatem accusantium doloremque laudantium, totam rem aperiam, eaque ipsa quae.</div>
  <div class="abs" style="left:0;top:160px;width:392px;height:60px;background:var(--forest)"></div>
  <div class="card" style="left:24px;top:83px;width:75px;height:108px"></div><div class="abs ph-face" role="img" aria-label="Team member portrait" style="left:24px;top:83px;width:75px;height:78px"></div><div class="abs cap" style="left:24px;top:167px;width:75px;text-align:center;font-size:4.2px">Marcus T. Ellery<br><span class="tiny">Position here</span></div>
  <div class="card" style="left:112px;top:83px;width:75px;height:108px"></div><div class="abs ph-face" role="img" aria-label="Team member portrait" style="left:112px;top:83px;width:75px;height:78px"></div><div class="abs cap" style="left:112px;top:167px;width:75px;text-align:center;font-size:4.2px">Owen R. Hartley<br><span class="tiny">Position here</span></div>
  <div class="card" style="left:200px;top:83px;width:75px;height:108px"></div><div class="abs ph-face" role="img" aria-label="Team member portrait" style="left:200px;top:83px;width:75px;height:78px"></div><div class="abs cap" style="left:200px;top:167px;width:75px;text-align:center;font-size:4.2px">Daniel S. Brooke<br><span class="tiny">Position here</span></div>
  <div class="card" style="left:288px;top:83px;width:75px;height:108px"></div><div class="abs ph-face" role="img" aria-label="Team member portrait" style="left:288px;top:83px;width:75px;height:78px"></div><div class="abs cap" style="left:288px;top:167px;width:75px;text-align:center;font-size:4.2px">Adrian V. Lowell<br><span class="tiny">Position here</span></div>
  <div class="foot" style="color:#cfd8d4">Insert your footer title here</div>
</div>

<!-- Row 3 -->
<div class="slide" style="left:4px;top:1443px">
  <div class="bar"><div class="brand">VARNOK</div><div class="copy">Copyright © VARNOK. All rights reserved.</div><div class="dot"></div></div>
  <div class="abs ph-hair" role="img" aria-label="Portrait of smiling team member" style="left:0;top:27px;width:170px;height:193px"></div>
  <div class="abs title" style="left:200px;top:64px;font-size:15px">Selene M. Varga</div>
  <div class="abs tiny" style="left:200px;top:98px">Skill text here</div><div class="abs tiny" style="left:330px;top:96px;font-size:4.5px">90%</div>
  <div class="abs" style="left:200px;top:105px;width:145px;height:4px;background:var(--forest)"></div>
  <div class="abs tiny" style="left:200px;top:127px">Skill text here</div><div class="abs tiny" style="left:330px;top:125px;font-size:4.5px">90%</div>
  <div class="abs" style="left:200px;top:134px;width:145px;height:4px;background:var(--forest)"></div>
  <div class="abs tiny" style="left:200px;top:156px">Skill text here</div><div class="abs tiny" style="left:330px;top:154px;font-size:4.5px">90%</div>
  <div class="abs" style="left:200px;top:163px;width:145px;height:4px;background:var(--forest)"></div>
  <div class="foot" style="left:170px">Insert your footer title here</div>
</div>
<div class="slide" style="left:403px;top:1443px">
  <div class="bar"><div class="brand">VARNOK</div><div class="copy">Copyright © VARNOK. All rights reserved.</div><div class="dot"></div></div>
  <div class="abs" style="left:0;top:27px;width:392px;height:68px;background:var(--forest)"></div>
  <div class="abs title" style="left:20px;top:40px;color:#fff">Case Studies of<br><em>Entrepreneurial Success</em></div>
  <div class="abs tiny-w" style="left:230px;top:45px;width:140px">Sed ut perspiciatis unde omnis iste natus error sit voluptatem accusantium doloremque laudantium, totam rem aperiam, eaque ipsa quae ab illo.</div>
  <div class="card" style="left:20px;top:88px;width:108px;height:40px"></div><div class="circ" style="left:27px;top:102px">A</div><div class="abs cap" style="left:44px;top:94px">Service One</div><div class="abs tiny" style="left:44px;top:101px;width:76px">Sed ut perspiciatis unde omnis iste natus error sit voluptatem.</div>
  <div class="card" style="left:135px;top:88px;width:108px;height:40px"></div><div class="circ" style="left:142px;top:102px">B</div><div class="abs cap" style="left:159px;top:94px">Service Two</div><div class="abs tiny" style="left:159px;top:101px;width:76px">Sed ut perspiciatis unde omnis iste natus error sit voluptatem.</div>
  <div class="card" style="left:250px;top:88px;width:108px;height:40px"></div><div class="circ" style="left:257px;top:102px">C</div><div class="abs cap" style="left:274px;top:94px">Service Three</div><div class="abs tiny" style="left:274px;top:101px;width:76px">Sed ut perspiciatis unde omnis iste natus error sit voluptatem.</div>
  <div class="card" style="left:20px;top:145px;width:108px;height:40px"></div><div class="circ" style="left:27px;top:159px">D</div><div class="abs cap" style="left:44px;top:151px">Service Four</div><div class="abs tiny" style="left:44px;top:158px;width:76px">Sed ut perspiciatis unde omnis iste natus error sit voluptatem.</div>
  <div class="card" style="left:135px;top:145px;width:108px;height:40px"></div><div class="circ" style="left:142px;top:159px">E</div><div class="abs cap" style="left:159px;top:151px">Service Five</div><div class="abs tiny" style="left:159px;top:158px;width:76px">Sed ut perspiciatis unde omnis iste natus error sit voluptatem.</div>
  <div class="card" style="left:250px;top:145px;width:108px;height:40px"></div><div class="circ" style="left:257px;top:159px">F</div><div class="abs cap" style="left:274px;top:151px">Service Six</div><div class="abs tiny" style="left:274px;top:158px;width:76px">Sed ut perspiciatis unde omnis iste natus error sit voluptatem.</div>
  <div class="foot">Insert your footer title here</div>
</div>
<div class="slide" style="left:802px;top:1443px">
  <div class="bar"><div class="brand">VARNOK</div><div class="copy">Copyright © VARNOK. All rights reserved.</div><div class="dot"></div></div>
  <div class="abs title" style="left:32px;top:58px">Case Studies of<br><em>Entrepreneurial Success</em></div>
  <svg class="abs" style="left:0;top:0" width="392" height="220" viewBox="0 0 392 220">
    <g font-size="3" fill="#8a8f8d"><text x="30" y="125">● 2024 ● 2025</text><text x="100" y="125">● 2024 ● 2025</text></g>
    <circle cx="63" cy="160" r="16" fill="none" stroke="#e3ece6" stroke-width="7"/>
    <circle cx="63" cy="160" r="16" fill="none" stroke="#6aa84f" stroke-width="7" stroke-dasharray="75 101" transform="rotate(-90 63 160)"/>
    <circle cx="63" cy="160" r="16" fill="none" stroke="#0f3b31" stroke-width="7" stroke-dasharray="26 101" stroke-dashoffset="-75" transform="rotate(-90 63 160)"/>
    <text x="63" y="161" font-size="4" text-anchor="middle" fill="#1e3d36">75%</text>
    <circle cx="133" cy="160" r="16" fill="none" stroke="#6aa84f" stroke-width="7" stroke-dasharray="61 101" transform="rotate(-90 133 160)"/>
    <circle cx="133" cy="160" r="16" fill="none" stroke="#0f3b31" stroke-width="7" stroke-dasharray="40 101" stroke-dashoffset="-61" transform="rotate(-90 133 160)"/>
    <text x="133" y="161" font-size="4" text-anchor="middle" fill="#1e3d36">60%</text>
    <g stroke="#eceeed" stroke-width=".4"><line x1="190" y1="50" x2="360" y2="50"/><line x1="190" y1="72" x2="360" y2="72"/><line x1="190" y1="94" x2="360" y2="94"/><line x1="190" y1="116" x2="360" y2="116"/><line x1="190" y1="138" x2="360" y2="138"/><line x1="190" y1="160" x2="360" y2="160"/><line x1="190" y1="182" x2="360" y2="182"/></g>
    <g fill="#8a8f8d" font-size="3"><text x="182" y="52">300</text><text x="182" y="96">200</text><text x="182" y="140">100</text><text x="185" y="183">0</text>
    <text x="200" y="190">Category 1</text><text x="242" y="190">Category 2</text><text x="284" y="190">Category 3</text><text x="326" y="190">Category 4</text></g>
    <rect x="198" y="165" width="6" height="17" fill="#00a9c4"/><rect x="205" y="73" width="6" height="109" fill="#0f3b31"/><rect x="212" y="140" width="6" height="42" fill="#8fd18a"/><rect x="219" y="160" width="6" height="22" fill="#00a9c4"/>
    <rect x="240" y="160" width="6" height="22" fill="#00a9c4"/><rect x="247" y="132" width="6" height="50" fill="#0f3b31"/><rect x="254" y="125" width="6" height="57" fill="#6aa84f"/><rect x="261" y="130" width="6" height="52" fill="#3f7a4f"/>
    <rect x="282" y="150" width="6" height="32" fill="#00a9c4"/><rect x="289" y="120" width="6" height="62" fill="#3f7a4f"/><rect x="296" y="92" width="6" height="90" fill="#8fd18a"/><rect x="303" y="130" width="6" height="52" fill="#00a9c4"/>
    <rect x="324" y="140" width="6" height="42" fill="#6aa84f"/><rect x="331" y="108" width="6" height="74" fill="#0f3b31"/><rect x="338" y="104" width="6" height="78" fill="#6aa84f"/><rect x="345" y="115" width="6" height="67" fill="#00a9c4"/>
  </svg>
  <div class="foot">Insert your footer title here</div>
</div>

<!-- Row 4 -->
<div class="slide" style="left:4px;top:1674px">
  <div class="bar"><div class="brand">VARNOK</div><div class="copy">Copyright © VARNOK. All rights reserved.</div><div class="dot"></div></div>
  <div class="abs title" style="left:46px;top:40px">Pricing Plan</div>
  <div class="abs tiny" style="left:160px;top:42px;width:170px">Sed ut perspiciatis unde omnis iste natus error sit voluptatem accusantium doloremque laudantium, totam rem aperiam, eaque ipsa quae ab illo inventore veritatis.</div>
  <div class="abs" style="left:46px;top:86px;font-family:Marcellus,serif;font-size:13px"><sup style="font-size:5px">$</sup>149 <span style="font-size:3.5px">/semester</span></div>
  <div class="abs" style="left:157px;top:86px;font-family:Marcellus,serif;font-size:13px"><sup style="font-size:5px">$</sup>249 <span style="font-size:3.5px">/semester</span></div>
  <div class="abs" style="left:264px;top:86px;font-family:Marcellus,serif;font-size:13px"><sup style="font-size:5px">$</sup>479 <span style="font-size:3.5px">/semester</span></div>
  <div class="abs" style="left:46px;top:107px;font-size:4px;color:var(--leaf)">Silver Package</div>
  <div class="abs" style="left:157px;top:107px;font-size:4px;color:var(--leaf)">Medium Package</div>
  <div class="abs" style="left:264px;top:107px;font-size:4px;color:var(--leaf)">Premium Package</div>
  <div class="abs tiny" style="left:46px;top:116px;width:72px">Sed ut perspiciatis unde omnis iste natus error sit voluptatem doloremque.<br>✓ Sed ut perspiciatis<br>✓ Natus error sit voluptatem<br>✓ Accusantium doloremque</div>
  <div class="abs tiny" style="left:157px;top:116px;width:72px">Sed ut perspiciatis unde omnis iste natus error sit voluptatem doloremque.<br>✓ Sed ut perspiciatis<br>✓ Natus error sit voluptatem<br>✓ Totam rem aperiam<br>✓ Accusantium doloremque</div>
  <div class="abs tiny" style="left:264px;top:116px;width:72px">Sed ut perspiciatis unde omnis iste natus error sit voluptatem doloremque.<br>✓ Sed ut perspiciatis<br>✓ Natus error sit voluptatem<br>✓ Totam rem aperiam<br>✓ Eaque ipsa quae<br>✓ Accusantium doloremque</div>
  <div class="btn" style="left:46px;top:184px;width:68px">Get Started<span style="float:right;margin-right:3px">→</span></div>
  <div class="btn" style="left:157px;top:190px;width:68px">Get Started<span style="float:right;margin-right:3px">→</span></div>
  <div class="btn" style="left:264px;top:196px;width:68px">Get Started<span style="float:right;margin-right:3px">→</span></div>
</div>
<div class="slide" style="left:403px;top:1674px">
  <div class="bar"><div class="brand">VARNOK</div><div class="copy">Copyright © VARNOK. All rights reserved.</div><div class="dot"></div></div>
  <div class="abs ph-car" role="img" aria-label="Portfolio car photo" style="left:16px;top:30px;width:115px;height:56px;border-radius:5px"></div>
  <div class="abs ph-car" role="img" aria-label="Portfolio car photo" style="left:137px;top:30px;width:115px;height:56px;border-radius:5px"></div>
  <div class="abs ph-car" role="img" aria-label="Portfolio car photo" style="left:258px;top:30px;width:115px;height:56px;border-radius:5px"></div>
  <div class="abs ph-car" role="img" aria-label="Portfolio car photo" style="left:16px;top:92px;width:115px;height:56px;border-radius:5px"></div>
  <div class="abs" style="left:137px;top:92px;width:115px;height:56px;border-radius:5px;background:var(--leaf)"></div>
  <div class="abs" style="left:137px;top:99px;width:115px;text-align:center;font-family:Marcellus,serif;font-size:12px;color:#fff">Our Portfolio</div>
  <div class="abs tiny-w" style="left:150px;top:118px;width:90px;text-align:center;color:#fff">Sed ut perspiciatis unde omnis iste natus error sit voluptatem accusantium, totam rem aperiam.</div>
  <div class="abs ph-car" role="img" aria-label="Portfolio car photo" style="left:258px;top:92px;width:115px;height:56px;border-radius:5px"></div>
  <div class="abs ph-car" role="img" aria-label="Portfolio car photo" style="left:16px;top:154px;width:115px;height:58px;border-radius:5px"></div>
  <div class="abs ph-car" role="img" aria-label="Portfolio car photo" style="left:137px;top:154px;width:115px;height:58px;border-radius:5px"></div>
  <div class="abs ph-car" role="img" aria-label="Portfolio car photo" style="left:258px;top:154px;width:115px;height:58px;border-radius:5px"></div>
</div>
<div class="slide" style="left:802px;top:1674px">
  <div class="bar"><div class="brand">VARNOK</div><div class="copy">Copyright © VARNOK. All rights reserved.</div><div class="dot"></div></div>
  <div class="abs" style="left:0;top:27px;width:110px;height:193px;background:var(--moss)"></div>
  <div class="abs ph-car" role="img" aria-label="Green car photo" style="left:28px;top:88px;width:50px;height:112px;border-radius:4px"></div>
  <div class="abs" style="left:60px;top:28px;width:90px;height:178px;border-radius:10px;background:#0b0f0d;padding:3px">
    <div class="ph-car" role="img" aria-label="Green car photo on phone screen" style="width:100%;height:100%;border-radius:8px"></div>
  </div>
  <div class="abs title" style="left:180px;top:68px">Case Studies of<br><em>Overcoming Disruptions</em></div>
  <div class="circ" style="left:180px;top:108px">A</div><div class="abs cap" style="left:200px;top:106px">Tittle text here</div><div class="abs tiny" style="left:200px;top:113px;width:60px">Lorem ipsum dolor sit amet, adipiscing elit porttitor congue.</div>
  <div class="circ" style="left:272px;top:108px">C</div><div class="abs cap" style="left:292px;top:106px">Tittle text here</div><div class="abs tiny" style="left:292px;top:113px;width:60px">Lorem ipsum dolor sit amet, adipiscing elit porttitor congue.</div>
  <div class="circ" style="left:180px;top:150px">B</div><div class="abs cap" style="left:200px;top:148px">Tittle text here</div><div class="abs tiny" style="left:200px;top:155px;width:60px">Lorem ipsum dolor sit amet, adipiscing elit porttitor congue.</div>
  <div class="circ" style="left:272px;top:150px">D</div><div class="abs cap" style="left:292px;top:148px">Tittle text here</div><div class="abs tiny" style="left:292px;top:155px;width:60px">Lorem ipsum dolor sit amet, adipiscing elit porttitor congue.</div>
  <div class="foot" style="left:110px">Insert your footer title here</div>
</div>

<!-- Row 5 -->
<div class="slide" style="left:4px;top:1906px">
  <div class="bar"><div class="brand">VARNOK</div><div class="copy">Copyright © VARNOK. All rights reserved.</div><div class="dot"></div></div>
  <div class="abs" style="left:0;top:100px;width:150px;height:120px;background:var(--moss)"></div>
  <div class="abs ph-car" role="img" aria-label="Green car photo" style="left:20px;top:48px;width:120px;height:66px;border-radius:5px"></div>
  <div class="abs ph-car" role="img" aria-label="Green car photo" style="left:148px;top:48px;width:52px;height:46px;border-radius:5px"></div>
  <div class="abs ph-car" role="img" aria-label="Green car photo" style="left:20px;top:124px;width:55px;height:36px;border-radius:5px"></div>
  <div class="abs ph-car" role="img" aria-label="Green car photo" style="left:85px;top:124px;width:55px;height:36px;border-radius:5px"></div>
  <div class="abs ph-car" role="img" aria-label="Green car photo" style="left:148px;top:102px;width:52px;height:56px;border-radius:5px"></div>
  <div class="abs title" style="left:222px;top:80px">Building a Reputation<br>That Attracts Top</div>
  <div class="abs tiny" style="left:222px;top:112px;width:135px">Sed ut perspiciatis unde omnis iste natus error sit voluptatem accusantium doloremque laudantium, totam rem aperiam, eaque ipsa quae ab illo inventore veritatis et quasi architecto.</div>
  <div class="abs tiny" style="left:222px;top:140px;width:135px">Sed ut perspiciatis unde omnis iste natus error sit voluptatem accusantium doloremque laudantium, totam rem aperiam, eaque ipsa quae ab illo.</div>
  <div class="foot" style="left:150px">Insert your footer title here</div>
</div>
<div class="slide" style="left:403px;top:1906px">
  <div class="bar"><div class="brand">VARNOK</div><div class="copy">Copyright © VARNOK. All rights reserved.</div><div class="dot"></div></div>
  <div class="abs title" style="left:22px;top:88px">Building a Motivated and<br>Productive Workforce</div>
  <div class="abs ph-car" role="img" aria-label="Green car photo" style="left:212px;top:35px;width:110px;height:80px;border-radius:6px"></div>
  <div class="abs ph-car" role="img" aria-label="Green car close-up" style="left:296px;top:76px;width:66px;height:64px;border-radius:6px;border:2px solid #fff"></div>
  <div class="abs" style="left:26px;top:148px;width:88px;height:2px;background:var(--leaf)"></div>
  <div class="abs ph-hair" role="img" aria-label="Small author portrait" style="left:26px;top:163px;width:16px;height:16px;border-radius:50%"></div>
  <div class="abs tiny" style="left:60px;top:166px;color:var(--ink)">Building a Motivated and<br>Productive Workforce</div>
  <div class="abs tiny" style="left:220px;top:150px;width:140px">Sed ut perspiciatis unde omnis iste natus error sit voluptatem accusantium doloremque laudantium, totam rem aperiam, eaque ipsa quae ab illo inventore veritatis et quasi architecto beatae vitae.</div>
  <div class="foot">Insert your footer title here</div>
</div>
<div class="slide" style="left:802px;top:1906px">
  <div class="bar"><div class="brand">VARNOK</div><div class="copy">Copyright © VARNOK. All rights reserved.</div><div class="dot"></div></div>
  <div class="abs title" style="left:20px;top:82px">Vision</div>
  <div class="abs tiny" style="left:20px;top:118px;width:120px">Sed ut perspiciatis unde omnis iste natus error sit voluptatem accusantium doloremque laudantium, totam rem aperiam, eaque ipsa quae ab illo inventore.</div>
  <div class="abs" style="left:165px;top:45px;width:92px;height:158px;border-radius:5px;background:var(--forest)"></div>
  <div class="abs ph-car" role="img" aria-label="Green car photo" style="left:169px;top:49px;width:84px;height:128px;border-radius:4px"></div>
  <div class="abs" style="left:174px;top:142px;width:70px;font-size:4px;color:#fff">Lorem ipsum dolor sit amet, consectetur adipiscing</div>
  <div class="abs" style="left:172px;top:188px;font-size:6px;color:#fff">↗</div><div class="abs" style="left:222px;top:190px;font-size:3.5px;color:#fff">Vision One</div>
  <div class="abs" style="left:268px;top:45px;width:92px;height:158px;border-radius:5px;background:var(--moss)"></div>
  <div class="abs ph-car" role="img" aria-label="Green car photo" style="left:272px;top:49px;width:84px;height:128px;border-radius:4px"></div>
  <div class="abs" style="left:277px;top:142px;width:72px;font-size:4px;color:#fff">Lorem ipsum decided to leave for the far World of Grammar.</div>
  <div class="abs" style="left:275px;top:188px;font-size:6px;color:#fff">↗</div><div class="abs" style="left:326px;top:190px;font-size:3.5px;color:#fff">Vision Two</div>
  <div class="foot">Insert your footer title here</div>
</div>

<!-- Row 6 -->
<div class="slide" style="left:4px;top:2137px">
  <div class="bar"><div class="brand">VARNOK</div><div class="copy">Copyright © VARNOK. All rights reserved.</div><div class="dot"></div></div>
  <div class="abs" style="left:32px;top:40px;width:74px;height:80px;border-radius:5px;background:var(--forest)"></div>
  <div class="abs" style="left:110px;top:40px;width:74px;height:80px;border-radius:5px;background:var(--leaf)"></div>
  <div class="abs" style="left:40px;top:60px;font-family:Marcellus,serif;font-size:12px;color:#fff">313<sup style="font-size:5px">+</sup></div>
  <div class="abs" style="left:118px;top:60px;font-family:Marcellus,serif;font-size:12px;color:#fff">539<sup style="font-size:5px">+</sup></div>
  <div class="abs" style="left:93px;top:45px;width:9px;height:9px;border-radius:50%;background:#fff"></div>
  <div class="abs" style="left:171px;top:45px;width:9px;height:9px;border-radius:50%;background:#fff"></div>
  <div class="abs tiny-w" style="left:40px;top:84px;width:60px;color:#fff">Lorem ipsum dolor sit amet, consectetur adipiscing elit. Maecenas porttitor congue massa.</div>
  <div class="abs tiny-w" style="left:118px;top:84px;width:60px;color:#fff">Lorem ipsum dolor sit amet, consectetur adipiscing elit. Maecenas porttitor congue massa.</div>
  <div class="abs ph-car" role="img" aria-label="Green car photo" style="left:32px;top:126px;width:180px;height:64px;border-radius:5px"></div>
  <div class="abs ph-car" role="img" aria-label="Green car photo" style="left:218px;top:126px;width:140px;height:64px;border-radius:5px"></div>
  <div class="abs title" style="left:208px;top:48px">Building a Motivated and<br>Productive Workforce</div>
  <div class="abs tiny" style="left:208px;top:80px;width:145px">Sed ut perspiciatis unde omnis iste natus error sit voluptatem accusantium doloremque laudantium, totam rem aperiam, eaque ipsa quae ab illo inventore veritatis.</div>
  <div class="foot">Insert your footer title here</div>
</div>
<div class="slide" style="left:403px;top:2137px">
  <div class="bar"><div class="brand">VARNOK</div><div class="copy">Copyright © VARNOK. All rights reserved.</div><div class="dot"></div></div>
  <div class="abs title" style="left:0;right:0;top:50px;text-align:center">Our Infographic <em>case study</em></div>
  <svg class="abs" style="left:0;top:0" width="392" height="220" viewBox="0 0 392 220">
    <g fill="none" stroke-width="5">
      <path d="M62 90 A24 24 0 1 0 86 114" stroke="#8fd18a"/><path d="M128 90 A24 24 0 1 0 152 114" stroke="#0f3b31"/><path d="M195 90 A24 24 0 1 0 219 114" stroke="#0f3b31"/><path d="M262 90 A24 24 0 1 0 286 114" stroke="#8fd18a"/><circle cx="329" cy="114" r="24" stroke="#b5b8b7"/>
    </g>
    <g><polygon points="84,124 94,124 89,132" fill="#8fd18a"/><polygon points="150,124 160,124 155,132" fill="#0f3b31"/><polygon points="217,124 227,124 222,132" fill="#0f3b31"/><polygon points="284,124 294,124 289,132" fill="#8fd18a"/></g>
    <g fill="none" stroke="#8fd18a" stroke-width="1.6"><path d="M57 120 a6 6 0 0 1 6 -6"/><path d="M57 120 a11 11 0 0 1 11 -11"/></g>
    <rect x="122" y="108" width="12" height="12" rx="1.5" fill="none" stroke="#0f3b31" stroke-width="1.6"/><rect x="125.5" y="111.5" width="5" height="5" fill="#0f3b31"/>
    <circle cx="195" cy="114" r="12" fill="#0f3b31"/><rect x="189" y="110" width="12" height="9" rx="1.5" fill="#fff"/><circle cx="195" cy="114.5" r="2.5" fill="#0f3b31"/>
    <rect x="256" y="107" width="12" height="4" rx="1" fill="#8fd18a"/><rect x="256" y="112.5" width="12" height="4" rx="1" fill="#8fd18a"/><rect x="256" y="118" width="12" height="4" rx="1" fill="#8fd18a"/>
    <rect x="321" y="108" width="14" height="9" rx="1" fill="none" stroke="#b5b8b7" stroke-width="1.4"/><rect x="336" y="110" width="4" height="9" rx="1" fill="none" stroke="#b5b8b7" stroke-width="1.2"/><line x1="325" y1="121" x2="332" y2="121" stroke="#b5b8b7" stroke-width="1.4"/>
    <g font-size="4" fill="#1e3d36" text-anchor="middle"><text x="62" y="150">Tittle text here</text><text x="128" y="150">Tittle text here</text><text x="195" y="150">Tittle text here</text><text x="262" y="150">Tittle text here</text><text x="329" y="150">Tittle text here</text></g>
    <g font-size="3" fill="#8a8f8d" text-anchor="middle">
      <text x="62" y="158">Sed ut perspiciatis unde</text><text x="62" y="162">omnis iste natus error</text>
      <text x="128" y="158">Sed ut perspiciatis unde</text><text x="128" y="162">omnis iste natus error</text>
      <text x="195" y="158">Sed ut perspiciatis unde</text><text x="195" y="162">omnis iste natus error</text>
      <text x="262" y="158">Sed ut perspiciatis unde</text><text x="262" y="162">omnis iste natus error</text>
      <text x="329" y="158">Sed ut perspiciatis unde</text><text x="329" y="162">omnis iste natus error</text>
    </g>
  </svg>
  <div class="foot">Insert your footer title here</div>
</div>
<div class="slide" style="left:802px;top:2137px">
  <div class="bar"><div class="brand">VARNOK</div><div class="copy">Copyright © VARNOK. All rights reserved.</div><div class="dot"></div></div>
  <div class="abs title" style="left:0;right:0;top:46px;text-align:center">Our Chart Slides</div>
  <svg class="abs" style="left:0;top:0" width="392" height="220" viewBox="0 0 392 220">
    <rect x="36" y="64" width="150" height="88" rx="3" fill="#fff" stroke="#eceeed"/>
    <rect x="208" y="64" width="150" height="88" rx="3" fill="#fff" stroke="#eceeed"/>
    <g font-size="3" fill="#8a8f8d"><text x="42" y="72">Tittle text here</text><text x="214" y="72">Tittle text here</text></g>
    <g font-size="6" font-family="Marcellus, serif" fill="#1e3d36"><text x="163" y="72">2024</text><text x="335" y="72">2025</text></g>
    <g stroke="#f0f2f1" stroke-width=".4"><line x1="45" y1="85" x2="180" y2="85"/><line x1="45" y1="105" x2="180" y2="105"/><line x1="45" y1="125" x2="180" y2="125"/><line x1="217" y1="85" x2="352" y2="85"/><line x1="217" y1="105" x2="352" y2="105"/><line x1="217" y1="125" x2="352" y2="125"/></g>
    <g>
      <rect x="54" y="125" width="5" height="20" fill="#8fd18a"/><rect x="60" y="115" width="5" height="30" fill="#00a9c4"/><rect x="66" y="132" width="5" height="13" fill="#0f3b31"/>
      <rect x="86" y="120" width="5" height="25" fill="#8fd18a"/><rect x="92" y="105" width="5" height="40" fill="#00a9c4"/><rect x="98" y="130" width="5" height="15" fill="#0f3b31"/>
      <rect x="118" y="118" width="5" height="27" fill="#8fd18a"/><rect x="124" y="110" width="5" height="35" fill="#00a9c4"/><rect x="130" y="128" width="5" height="17" fill="#0f3b31"/>
      <rect x="150" y="108" width="5" height="37" fill="#8fd18a"/><rect x="156" y="90" width="5" height="55" fill="#00a9c4"/><rect x="162" y="125" width="5" height="20" fill="#0f3b31"/>
      <rect x="226" y="125" width="5" height="20" fill="#8fd18a"/><rect x="232" y="115" width="5" height="30" fill="#00a9c4"/><rect x="238" y="132" width="5" height="13" fill="#0f3b31"/>
      <rect x="258" y="120" width="5" height="25" fill="#8fd18a"/><rect x="264" y="105" width="5" height="40" fill="#00a9c4"/><rect x="270" y="130" width="5" height="15" fill="#0f3b31"/>
      <rect x="290" y="118" width="5" height="27" fill="#8fd18a"/><rect x="296" y="110" width="5" height="35" fill="#00a9c4"/><rect x="302" y="128" width="5" height="17" fill="#0f3b31"/>
      <rect x="322" y="108" width="5" height="37" fill="#8fd18a"/><rect x="328" y="90" width="5" height="55" fill="#00a9c4"/><rect x="334" y="125" width="5" height="20" fill="#0f3b31"/>
    </g>
  </svg>
  <div class="abs tiny" style="left:44px;top:162px;width:304px;text-align:center">Sed ut perspiciatis unde omnis iste natus error sit voluptatem accusantium doloremque laudantium, totam rem aperiam, eaque ipsa quae ab illo inventore veritatis et quasi architecto beatae vitae dicta sunt explicabo. Nemo enim ipsam voluptatem quia voluptas sit aspernatur aut odit aut fugit.</div>
  <div class="foot">Insert your footer title here</div>
</div>

<!-- Row 7 -->
<div class="slide" style="left:4px;top:2371px">
  <div class="bar"><div class="brand">VARNOK</div><div class="copy">Copyright © VARNOK. All rights reserved.</div><div class="dot"></div></div>
  <svg class="abs" style="left:0;top:0" width="392" height="220" viewBox="0 0 392 220">
    <g stroke="#eceeed" stroke-width=".4"><line x1="38" y1="45" x2="210" y2="45"/><line x1="38" y1="68" x2="210" y2="68"/><line x1="38" y1="91" x2="210" y2="91"/><line x1="38" y1="114" x2="210" y2="114"/><line x1="38" y1="137" x2="210" y2="137"/><line x1="38" y1="160" x2="210" y2="160"/><line x1="38" y1="183" x2="210" y2="183"/></g>
    <g font-size="3" fill="#8a8f8d"><text x="30" y="46">6</text><text x="30" y="69">5</text><text x="30" y="92">4</text><text x="30" y="115">3</text><text x="30" y="138">2</text><text x="30" y="161">1</text><text x="30" y="184">0</text>
    <text x="46" y="192">Category 1</text><text x="88" y="192">Category 2</text><text x="130" y="192">Category 3</text><text x="172" y="192">Category 4</text></g>
    <rect x="48" y="83" width="6" height="100" fill="#6aa84f"/><rect x="55" y="128" width="6" height="55" fill="#8fd18a"/><rect x="62" y="137" width="6" height="46" fill="#00a9c4"/>
    <rect x="90" y="125" width="6" height="58" fill="#6aa84f"/><rect x="97" y="65" width="6" height="118" fill="#8fd18a"/><rect x="104" y="137" width="6" height="46" fill="#00a9c4"/>
    <rect x="132" y="103" width="6" height="80" fill="#6aa84f"/><rect x="139" y="114" width="6" height="69" fill="#8fd18a"/><rect x="146" y="91" width="6" height="92" fill="#00a9c4"/>
    <rect x="174" y="68" width="6" height="115" fill="#6aa84f"/><rect x="181" y="114" width="6" height="69" fill="#8fd18a"/><rect x="188" y="45" width="6" height="138" fill="#00a9c4"/>
  </svg>
  <div class="abs title" style="left:240px;top:66px">Chart Enhancing<br>Performance</div>
  <div class="abs tiny" style="left:240px;top:98px;width:120px">Sed ut perspiciatis unde omnis iste natus error sit voluptatem accusantium doloremque laudantium, totam rem aperiam, eaque ipsa quae ab illo.</div>
  <div class="abs" style="left:240px;top:140px;font-family:Marcellus,serif;font-size:12px">340K</div>
  <div class="abs" style="left:296px;top:140px;font-family:Marcellus,serif;font-size:12px">139<sup style="font-size:5px">+</sup></div>
  <div class="abs tiny" style="left:240px;top:157px">Visitors</div><div class="abs tiny" style="left:296px;top:157px">Clients</div>
  <div class="foot">Insert your footer title here</div>
</div>
<div class="slide" style="left:410px;top:2371px;width:385px">
  <div class="bar"><div class="brand">VARNOK</div><div class="copy">Copyright © VARNOK. All rights reserved.</div><div class="dot"></div></div>
  <div class="abs title" style="left:0;right:0;top:44px;text-align:center">Our chart</div>
  <svg class="abs" style="left:0;top:0" width="385" height="220" viewBox="0 0 385 220">
    <defs><linearGradient id="areaFill" x1="0" y1="0" x2="0" y2="1"><stop offset="0" stop-color="#6aa84f"/><stop offset="1" stop-color="#ffffff" stop-opacity="0"/></linearGradient></defs>
    <g stroke="#eceeed" stroke-width=".4"><line x1="30" y1="75" x2="360" y2="75"/><line x1="30" y1="105" x2="360" y2="105"/><line x1="30" y1="135" x2="360" y2="135"/><line x1="30" y1="165" x2="360" y2="165"/><line x1="30" y1="195" x2="360" y2="195"/></g>
    <g font-size="3" fill="#8a8f8d"><text x="22" y="76">150</text><text x="22" y="106">100</text><text x="22" y="136">50</text><text x="24" y="196">0</text></g>
    <path d="M30 185 L60 175 L80 182 L100 165 L120 178 L140 160 L160 175 L180 150 L195 165 L210 130 L225 85 L238 120 L250 100 L265 140 L285 150 L305 165 L325 170 L345 175 L360 182 L360 195 L30 195 Z" fill="url(#areaFill)" opacity=".7"/>
    <polyline points="30,185 60,175 80,182 100,165 120,178 140,160 160,175 180,150 195,165 210,130 225,85 238,120 250,100 265,140 285,150 305,165 325,170 345,175 360,182" fill="none" stroke="#0f3b31" stroke-width=".8"/>
    <polyline points="30,190 60,183 80,188 100,178 120,186 140,172 160,182 180,165 195,172 210,150 225,118 238,140 250,128 265,158 285,162 305,176 325,178 345,183 360,188" fill="none" stroke="#8fd18a" stroke-width=".8"/>
  </svg>
  <div class="foot">Insert your footer title here</div>
</div>
<div class="slide" style="left:808px;top:2371px;background:var(--forest)">
  <div class="abs gold-word" style="left:18px;top:24px;font-size:38px">VARNOK</div>
  <div class="abs" style="left:18px;top:62px;font-family:Marcellus,serif;font-size:32px;color:#fff">Thank You</div>
  <div class="abs" style="left:210px;top:118px;width:70px;height:1px;background:#7fa39a"></div>
  <div class="abs tiny-w" style="left:292px;top:110px;width:88px">Sed ut perspiciatis unde omnis iste natus error sit voluptatem accusantium laudantium, totam rem.</div>
  <div class="abs" style="left:0;top:146px;width:392px;height:74px;background:var(--forest-mid)"></div>
  <div class="abs tiny-w" style="left:70px;top:172px;text-align:center;font-size:4.5px">Address<br>482 Linden Row<br>Harlow, MA 02194</div>
  <div class="abs tiny-w" style="left:175px;top:172px;text-align:center;font-size:4.5px">Email<br>hello@varnok.com<br>team@varnok.com</div>
  <div class="abs tiny-w" style="left:285px;top:172px;text-align:center;font-size:4.5px">Phone &amp; Fax<br>+1 (555) 014 2290<br>555 014 2291</div>
  <div class="foot" style="color:#cfd8d4">Insert your footer title here</div>
</div>

</body>
</html>
```